Lanternfield Drinks business cards

We need a business card design for our new logo. The company is modern, progressive, professional, yet approachable. The key products are ready to drink bottles and cans of coffee based beverages.
These cards will be a critical part of the first impression made by our sales organization, business development team, and all external facing personnel.
Card can be a vertical or horizontal orientation.

Target Market(s)

Customers, suppliers, business partners

Industry/Entity Type

Business

Contact Information for Business Card

Business cards should feature Company Name and Logo.

Font styles to use
Serif

Colors

Designer to choose colors to be used in the design.

Requirements
Must have
• Strong readability of Name, phone #, mobile number and email address.
• Job title, website url, Street Address, and other details can be secondary level readability.
Nice to have
• High impact, simplistic quality design.
• Ok to utilize the 'H in the box' separate from the company name

```html
<!DOCTYPE html>
<html lang="en">
<head>
<meta charset="utf-8">
<title>Lanternfield Drinks business cards</title>
<link rel="stylesheet" href="https://fonts.googleapis.com/css2?family=Crimson+Text:wght@400;600&display=swap">
<style>
  :root {
    --backdrop: #c9c9c9;
    --orange-top: #de8734;
    --orange-bottom: #c5502b;
    --orange-mid: #d8662c;
    --brand-red: #c84a22;
    --paper: #f3f3f1;
    --ink-light: #fdf6ef;
    --edge-dark: #1c1410;
  }
  html, body {
    margin: 0;
    padding: 0;
    overflow: hidden;
  }
  body {
    width: 1200px;
    height: 576px;
    background: var(--backdrop);
    position: relative;
    font-family: "Crimson Text", Georgia, serif;
  }
  .card {
    position: absolute;
    border-radius: 14px;
    overflow: hidden;
  }

  /* Front */
  .card-front {
    left: 82px;
    top: 138px;
    width: 484px;
    height: 294px;
    background: linear-gradient(180deg, var(--orange-top) 0%, var(--orange-mid) 60%, var(--orange-bottom) 100%);
  }
  .front-brand {
    position: absolute;
    left: 0;
    right: 0;
    top: 78px;
    text-align: center;
    color: var(--ink-light);
  }
  .brand-square {
    display: block;
    width: 74px;
    height: 74px;
    margin: 0 auto 14px;
    border: 3px solid var(--ink-light);
    box-sizing: border-box;
  }
  .front-name {
    font-size: 33px;
    font-weight: 600;
    letter-spacing: 1px;
    line-height: 1;
  }
  .front-sub {
    display: flex;
    align-items: center;
    justify-content: center;
    gap: 8px;
    width: 262px;
    margin: 4px auto 0;
    font-size: 11px;
    font-weight: 600;
    letter-spacing: 1.5px;
    line-height: 1;
  }
  .front-sub::before,
  .front-sub::after {
    content: "";
    flex: 1;
    height: 1.5px;
    background: var(--ink-light);
  }

  /* Back */
  .card-back {
    left: 602px;
    top: 138px;
    width: 481px;
    height: 291px;
  }
  .back-shape {
    position: absolute;
    inset: 0;
  }
  .holder {
    position: absolute;
    left: 28px;
    top: 23px;
    color: var(--ink-light);
  }
  .holder-name {
    font-size: 19px;
    font-weight: 600;
    line-height: 1;
  }
  .holder-title {
    font-size: 12.5px;
    margin-top: 5px;
  }
  .contact-list {
    position: absolute;
    left: 28px;
    top: 172px;
    margin: 0;
    padding: 0;
    list-style: none;
    color: var(--ink-light);
    font-size: 13px;
    line-height: 17px;
  }
  .contact-list li {
    display: flex;
    align-items: center;
    gap: 12px;
  }
  .contact-list svg {
    width: 11px;
    height: 11px;
    fill: var(--ink-light);
  }
  .address {
    position: absolute;
    left: 28px;
    top: 245px;
    color: var(--ink-light);
    font-size: 13px;
  }
  .back-square {
    position: absolute;
    left: 343px;
    top: 117px;
    width: 56px;
    height: 56px;
    border: 3px solid var(--brand-red);
    box-sizing: border-box;
  }
  .back-wordmark {
    position: absolute;
    left: 428px;
    top: 145px;
    transform: translate(-50%, -50%) rotate(-90deg);
    color: var(--brand-red);
    text-align: center;
    white-space: nowrap;
  }
  .back-name {
    font-size: 24px;
    font-weight: 600;
    letter-spacing: 0.5px;
    line-height: 1;
  }
  .back-sub {
    display: flex;
    align-items: center;
    gap: 6px;
    margin-top: 3px;
    font-size: 8.5px;
    font-weight: 600;
    letter-spacing: 1.2px;
    line-height: 1;
  }
  .back-sub::before,
  .back-sub::after {
    content: "";
    flex: 1;
    height: 1.5px;
    background: var(--brand-red);
  }
</style>
</head>
<body>
  <section class="card card-front" aria-label="Card front">
    <div class="front-brand">
      <span class="brand-square"></span>
      <div class="front-name">LANTERNFIELD</div>
      <div class="front-sub">DRINKS CO</div>
    </div>
  </section>

  <section class="card card-back" aria-label="Card back">
    <svg class="back-shape" viewBox="0 0 481 291" preserveAspectRatio="none" aria-hidden="true">
      <defs>
        <linearGradient id="backOrange" x1="0" y1="0" x2="0" y2="1">
          <stop offset="0" stop-color="#dc7a31"/>
          <stop offset="1" stop-color="#cf5a2a"/>
        </linearGradient>
      </defs>
      <rect width="481" height="291" fill="url(#backOrange)"/>
      <path d="M332 0 Q262 145 326 291 L481 291 L481 0 Z" fill="var(--edge-dark)"/>
      <path d="M332 0 Q272 145 334 291 L481 291 L481 0 Z" fill="var(--paper)"/>
    </svg>

    <div class="holder">
      <div class="holder-name">John Doe Smith</div>
      <div class="holder-title">Managing Director</div>
    </div>

    <ul class="contact-list">
      <li>
        <svg viewBox="0 0 12 12"><path d="M1 4 Q6 0 11 4 L9.5 5.5 L8 4.5 L8 3.5 Q6 2.8 4 3.5 L4 4.5 L2.5 5.5 Z M2.5 7 H9.5 V11 H2.5 Z"/></svg>
        <span>555.555.5555</span>
      </li>
      <li>
        <svg viewBox="0 0 12 12"><path d="M3 0.5 H9 V11.5 H3 Z M4 1.8 V9 H8 V1.8 Z M5.5 9.8 H6.5 V10.8 H5.5 Z"/></svg>
        <span>666.666.7777</span>
      </li>
      <li>
        <svg viewBox="0 0 12 12"><path d="M0.5 2.5 H11.5 V9.5 H0.5 Z M1.5 3.5 L6 7 L10.5 3.5 V8.5 H1.5 Z"/></svg>
        <span>johndoe@yourwebsite.com</span>
      </li>
      <li>
        <svg viewBox="0 0 12 12"><path d="M6 0.5 A5.5 5.5 0 1 0 6.01 0.5 Z M6 1.5 A4.5 4.5 0 1 1 5.99 1.5 Z M5.5 1.5 H6.5 V10.5 H5.5 Z M1.5 5.5 H10.5 V6.5 H1.5 Z"/></svg>
        <span>www.yourwebsite.com</span>
      </li>
    </ul>

    <div class="address">234 Anywhere St., Any Town, US 123456</div>

    <span class="back-square"></span>
    <div class="back-wordmark">
      <div class="back-name">LANTERNFIELD</div>
      <div class="back-sub">DRINKS CO</div>
    </div>
  </section>
</body>
</html>
```